Now Leasing Banner

Looking for a banner that says the following information approx 4' x 30'

Now Leasing Maplebrook Terrace 925-318-6042

Target Market(s)

Drive by traffic

Industry/Entity Type

Residential property management

Requirements
Must have
• Clear and readable from a distance

```html
<!DOCTYPE html>
<html lang="en">
<head>
<meta charset="utf-8">
<title>Now Leasing Banner – Maplebrook Terrace</title>
<link rel="stylesheet" href="https://fonts.googleapis.com/css2?family=Montserrat:wght@800&family=Fira+Sans+Extra+Condensed:wght@700&display=swap">
<style>
  :root {
    --banner-red: #e41e26;
    --panel-white: #f2f2f4;
    --ink-black: #000000;
    --page-bg: #ffffff;
  }
  html, body {
    margin: 0;
    padding: 0;
    width: 1200px;
    height: 662px;
    overflow: hidden;
    background: var(--page-bg);
  }
  .stage {
    width: 1200px;
    height: 662px;
    display: flex;
    align-items: center;
    justify-content: center;
  }
  .banner {
    width: 1140px;
    height: auto;
    display: block;
    filter: drop-shadow(8px 10px 8px rgba(0,0,0,0.28));
  }
  .banner-frame { fill: var(--banner-red); }
  .banner-panel { fill: var(--panel-white); }
  .now-tag { fill: var(--ink-black); }
  .now-label {
    fill: var(--panel-white);
    font-family: "Montserrat", sans-serif;
    font-weight: 800;
    font-size: 58px;
  }
  .headline {
    fill: var(--ink-black);
    font-family: "Montserrat", sans-serif;
    font-weight: 800;
    font-size: 292px;
  }
  .property-name, .property-phone {
    fill: var(--ink-black);
    font-family: "Fira Sans Extra Condensed", sans-serif;
    font-weight: 700;
    font-size: 132px;
  }
</style>
</head>
<body>
  <main class="stage">
    <svg class="banner" viewBox="0 0 2344 313" xmlns="http://www.w3.org/2000/svg" aria-label="Now Leasing banner, Maplebrook Terrace, 925-318-6042">
      <defs>
        <filter id="text-shadow" x="-5%" y="-10%" width="115%" height="130%">
          <feDropShadow dx="7" dy="7" stdDeviation="4" flood-color="#000" flood-opacity="0.3"/>
        </filter>
      </defs>
      <rect class="banner-frame" x="0" y="0" width="2344" height="313"/>
      <rect class="banner-panel" x="32" y="27" width="2280" height="260" rx="55" ry="55"/>

      <g filter="url(#text-shadow)">
        <rect class="now-tag" x="82" y="54" width="62" height="208"/>
        <text class="now-label" x="113" y="158" text-anchor="middle" dominant-baseline="central" transform="rotate(-90 113 158)" textLength="150" lengthAdjust="spacingAndGlyphs">NOW</text>

        <text class="headline" x="144" y="262" textLength="1303" lengthAdjust="spacingAndGlyphs">LEASING</text>

        <text class="property-name" x="1472" y="144" textLength="772" lengthAdjust="spacingAndGlyphs">Maplebrook Terrace</text>
        <text class="property-phone" x="1482" y="262" textLength="752" lengthAdjust="spacingAndGlyphs">925-318-6042</text>
      </g>
    </svg>
  </main>
</body>
</html>
```